Backup Software Tri-fold Brochure Project

We need a great looking and informative brochure to describe our new Backup Software offering. The brochures are to be used in retail and small business environments given to clients interested in protecting their computer from data loss.
The brochure should include attractive imagery that conveys a sense of Trust and Security to the prospective client.
The copy is provided as an attachment to this project. We'd like our Brisk Harbor product logo to be printed on the back cover. The logo is attached to this project.
The finished tri-fold brochure will be submitted to Loomcraft for printing as an 8.5" x 11" tri-fold brochure. Their design instructions are online http://loomcraft-example.com/custom-brochures.aspx.
The finished product should be Adobe Illustrator CS3 (*.ai) with a PDF Proof.
Target Market(s)
Retail and Small Business customers
Industry/Entity Type
Software
Colors
Designer to choose colors to be used in the design.
Look and feel

```html
<!DOCTYPE html>
<html lang="en">
<head>
<meta charset="utf-8">
<title>Brisk Harbor Offsite Backup – Tri-fold Brochure</title>
<link rel="stylesheet" href="https://fonts.googleapis.com/css2?family=Lato:wght@400;700&family=Roboto+Condensed:wght@400;700&display=swap">
<style>
:root{
  --green:#6cbf45;
  --green-dark:#4fa12e;
  --blue:#1f63ad;
  --blue-dark:#174f8f;
  --ink:#2a2a2a;
  --text:#333;
  --footer:#2e2b2b;
  --paper:#fff;
  --paper-shade:#e9e9e9;
  --stage:#f2f2f2;
}
*{box-sizing:border-box;margin:0;padding:0}
html,body{width:1200px;height:1200px;overflow:hidden;background:var(--stage)}
body{position:relative;font-family:"Lato",sans-serif;color:var(--text)}
.sheet{position:absolute;left:234px;width:717px;height:560px;background:var(--paper);box-shadow:0 6px 18px rgba(0,0,0,.18);overflow:hidden}
.sheet--outside{top:27px}
.sheet--inside{top:615px}
.panel{position:absolute;top:0;height:560px;overflow:hidden}
.panel--left{left:0;width:244px}
.panel--mid{left:244px;width:230px}
.panel--right{left:474px;width:243px}
.body-copy{position:absolute;font-size:10.3px;line-height:12.6px;text-align:justify;color:var(--text)}
.body-copy p+p{margin-top:12.6px}
.footer{position:absolute;left:0;right:0;bottom:0;height:30px;background:var(--footer);color:#ddd;font-size:6.5px;display:flex;align-items:center;justify-content:center;letter-spacing:.1px}
.photo{position:absolute}
.heading{font-family:"Roboto Condensed",sans-serif;font-weight:700;color:var(--blue);font-size:10.5px;text-transform:uppercase;position:absolute}

/* outside sheet */
.outside-left{background:linear-gradient(90deg,#fff 0%,#fff 80%,#e6e6e6 100%)}
.outside-left .photo{left:0;bottom:0;width:244px;height:150px;background:linear-gradient(180deg,rgba(255,255,255,1) 0%,#e4e6ea 35%,#b9bec6 100%)}
.cover-mid .band{position:absolute;left:0;top:0}
.tagline{position:absolute;left:0;width:230px;top:34px;text-align:center;color:#fff;font-family:"Roboto Condensed",sans-serif;line-height:1.15}
.tagline .l1{font-size:19px;font-weight:700;display:block}
.tagline .l2{font-size:24px;font-weight:400;display:block}
.brand{position:absolute;left:0;width:230px;top:395px;text-align:center;display:flex;align-items:center;justify-content:center;gap:8px}
.brand .mark{width:14px;height:14px;background:var(--green)}
.brand .name{font-family:"Roboto Condensed",sans-serif;font-weight:700;font-size:25px;color:var(--blue)}
.brand-sub{position:absolute;left:0;width:230px;top:428px;text-align:center;font-size:9.5px;letter-spacing:3.5px;color:var(--blue);text-transform:uppercase}
.copyright{position:absolute;left:0;width:230px;top:487px;text-align:center;font-size:8.3px;line-height:11px;color:#333}
.cover-right{background:linear-gradient(90deg,#dcdcdc 0%,#f4f4f4 18%,#fff 60%)}
.cover-title{position:absolute;left:0;width:243px;text-align:center;font-family:"Roboto Condensed",sans-serif;font-weight:700}
.cover-title .t1{position:absolute;top:360px;left:0;width:243px;font-size:35px;color:var(--ink)}
.cover-title .t2{position:absolute;top:398px;left:0;width:243px;font-size:23px;color:var(--green)}
.cover-title .t3{position:absolute;top:418px;left:0;width:243px;font-size:90px;color:var(--blue);letter-spacing:-1px;line-height:1}

/* inside sheet */
.inside-left .faint-name{position:absolute;left:22px;top:46px;font-family:"Roboto Condensed",sans-serif;font-weight:700;font-size:28px;color:rgba(255,255,255,.18);line-height:1}
.options-title{top:192px;left:25px}
.options-sub{position:absolute;left:25px;top:210px;font-size:10.5px;line-height:12.6px;color:var(--blue)}
.options-list{position:absolute;left:25px;top:244px;width:196px;list-style:none;font-size:10.3px;line-height:12.6px}
.options-list li{position:relative;padding-left:16px;text-align:justify}
.options-list li+li{margin-top:12.6px}
.options-list li::before{content:"";position:absolute;left:1px;top:3px;width:7px;height:7px;border-radius:50%;background:var(--blue-dark)}
.cta{position:absolute;left:0;width:230px;text-align:center;color:#fff}
.cta .label{position:absolute;left:0;width:230px;top:395px;font-family:"Roboto Condensed",sans-serif;font-weight:700;font-size:9.5px;color:var(--green)}
.cta .main{position:absolute;left:0;width:230px;top:409px;font-size:15.5px;line-height:18px}
.cta .or{position:absolute;left:0;width:230px;top:452px;font-size:10px}
.cta .detail{position:absolute;left:14px;width:202px;top:472px;font-size:10.3px;line-height:12.6px}
</style>
</head>
<body>

<!-- Outside: inner flap, back cover, front cover -->
<section class="sheet sheet--outside">
  <div class="panel panel--left outside-left">
    <div class="body-copy" style="left:25px;top:38px;width:201px">
      <p>Your computer stores everything you've ever created. Everything you've written, every email you've sent, every list you've made, every picture you've taken or movie you've made, all music you've created, your proposals, your spreadsheets, your presentations, your word files, your artwork, programs you've written, anything you've dictated, and much more... All your digital life is stored on your computer and is at risk of loss without backup.</p>
      <p>And your computer stores a copy of all your personal information. Your passwords, your online banking, your PINs, your credit cards and all your health and shopping records. This makes it a juicy target for hackers. Every day your digital life is exposed to computer Viruses, Malware and spammers all trying to break in. If they succeed the damage could be incalculable.</p>
      <p>If hackers destroy your information or a simple hard drive failure happens, restoring your programs will cost you days of effort and potentially hundreds of dollars. But your files could be unrecoverable. This means the loss of everything you've ever created.</p>
    </div>
    <div class="photo" role="img" aria-label="Business people signing documents at a desk, with a set of keys"></div>
  </div>

  <div class="panel panel--mid cover-mid">
    <svg class="band" width="230" height="560" viewBox="0 0 230 560" aria-hidden="true">
      <polygon points="0,0 230,0 230,310 190,300 115,330 0,345" fill="var(--green)"/>
      <polygon points="0,345 115,330 190,300 230,310 230,325 115,345 0,360" fill="#e5e5e5"/>
    </svg>
    <div class="photo" role="img" aria-label="Green-tinted photo of a hand attaching a padlock to a server rack" style="left:0;top:86px;width:230px;height:222px;background:linear-gradient(160deg,#7fcb5a 0%,#5eae3c 55%,#4a9a2c 100%)"></div>
    <h2 class="tagline"><span class="l1">The only protection</span><span class="l2">is a great backup</span></h2>
    <div class="brand"><span class="mark"></span><span class="name">Brisk Harbor</span></div>
    <div class="brand-sub">Offsite Backup</div>
    <p class="copyright">Copyright(c) 2017, Tidewell Systems, Inc.<br>All Rights Reserved</p>
    <div class="footer">research.example-lab.org/archive/disk_failures.pdf</div>
  </div>

  <div class="panel panel--right cover-right">
    <div class="photo" role="img" aria-label="Cupped hands sheltering a young seedling growing in soil" style="left:0;top:0;width:243px;height:330px;background:linear-gradient(180deg,#3b3f48 0%,#8a8f98 45%,#c9b8a8 75%,#e8e4e0 100%)"></div>
    <svg style="position:absolute;left:0;top:0" width="243" height="400" viewBox="0 0 243 400" aria-hidden="true">
      <polygon points="0,330 60,300 243,255 243,345 150,310" fill="var(--blue)"/>
      <polygon points="0,330 150,310 243,345 243,400 0,400" fill="#f2f2f2"/>
      <polygon points="0,326 60,300 60,304 0,332" fill="var(--green)"/>
    </svg>
    <h1 class="cover-title"><span class="t1">Your entire</span><span class="t2">Digital Life is at</span><span class="t3">RISK</span></h1>
    <div class="footer">www.example-devices.com/downloads/services/lost_laptop_study.pdf</div>
  </div>
</section>

<!-- Inside: three inner panels -->
<section class="sheet sheet--inside">
  <div class="panel panel--left inside-left">
    <svg style="position:absolute;left:0;top:0" width="244" height="190" viewBox="0 0 244 190" aria-hidden="true">
      <polygon points="0,0 244,0 244,175 0,110" fill="var(--green)"/>
      <line x1="0" y1="110" x2="244" y2="175" stroke="var(--blue)" stroke-width="2.5"/>
    </svg>
    <div class="faint-name">Brisk Harbor</div>
    <h3 class="heading" style="left:25px;top:172px">We have what you need</h3>
    <div class="body-copy" style="left:25px;top:195px;width:197px">
      <p>We can create a snapshot of all the programs and files on your computer using our Image Backup technology. We'll give you your backup on an external hard drive which you can store someplace safe. If anything happens, just bring in your computer and your Image Backup and we'll restore your computer back to the point when the snapshot was taken.</p>
      <p>Restoring from an Image Backup is like setting your computer back in time. To make sure all your new files are protected, we'll also install Tidewell's Brisk Harbor software to backup your files every night. These backups are stored in Tidewell's secure datacenter to protect you from even the most severe data loss scenarios.</p>
      <p>The combination of your Image Backup and your nightly backup will ensure you have complete protection for both your programs and your files. It means complete peace of mind.</p>
    </div>
    <div class="footer">www.example-crimewatch.org/media/annualreport/2016_Report.pdf</div>
  </div>

  <div class="panel panel--mid">
    <div class="photo" role="img" aria-label="Businessman with a laptop in a server room touching floating digital screens" style="left:0;top:0;width:230px;height:190px;background:linear-gradient(180deg,#5b6d86 0%,#9fb2c8 50%,#dfe7ef 85%,#fff 100%)"></div>
    <h3 class="heading options-title">Options</h3>
    <p class="options-sub">Our Image Backup technology<br>can protect</p>
    <ul class="options-list">
      <li>Paneview PC's and Laptops running Paneview 7 and above (Paneview 8, 10+)</li>
      <li>Paneview Servers running Paneview 2008 and above (Paneview 2012, 2016+)</li>
    </ul>
    <svg style="position:absolute;left:0;top:325px" width="230" height="235" viewBox="0 0 230 235" aria-hidden="true">
      <polygon points="0,60 230,0 230,235 0,235" fill="var(--blue)"/>
      <polygon points="0,56 230,-4 230,6 0,66" fill="var(--green)"/>
    </svg>
    <div class="cta">
      <span class="label">WHAT TO DO</span>
      <p class="main">Call us to schedule a day<br>to bring in your computer</p>
      <p class="or">OR</p>
      <p class="detail">Once a month we do "Image Backup Saturday". Drop off your computer in the morning and pick it up a few hours later. Call for a copy of our schedule.</p>
    </div>
  </div>

  <div class="panel panel--right">
    <h3 class="heading" style="left:33px;top:36px">How it works</h3>
    <div class="body-copy" style="left:33px;top:62px;width:178px">
      <p>Our technology is designed to take advantage of the powerful imaging technology embedded in Northgate Paneview. Deep within the core of the OS is an imaging engine that can create a point-in-time backup of the Paneview Operating System, device drivers, programs and system state. The backup can be used later to recover the system back to this point-in-time.</p>
      <p>Backups created by our Imaging technology can even be used to restore Paneview to dissimilar hardware. This is a quick way to migrate to a new computer without having to reinstall everything from scratch.</p>
      <p>Our technology stores backups as Northgate "Virtual Hard Disk" (VHD). These VHD files can be directly mounted from the Paneview Disk Manager. This is a great way to browse the contents of your Image Backup and restore individual files and folders.</p>
    </div>
    <div class="photo" role="img" aria-label="An adult hand gently holding a baby's hand" style="left:0;bottom:0;width:243px;height:175px;background:linear-gradient(180deg,#fff 0%,#f3e3d3 40%,#d9a97e 80%,#c08a5e 100%)"></div>
  </div>
</section>

</body>
</html>
```